Global (re)insurance broker needs a business card design

We need a classic business card for our company that is headquartered in SG, with offices in Malaysia and Dubai. We specialise in insurance and reinsurance broking and consultancy for our global clients.

```html
<!DOCTYPE html>
<html lang="en">
<head>
<meta charset="utf-8">
<title>Korven — Business Card</title>
<link rel="stylesheet" href="https://fonts.googleapis.com/css2?family=Montserrat:wght@700&family=Open+Sans:wght@400&display=swap">
<style>
  :root {
    --backdrop: #2b2b2f;
    --card: #161616;
    --brand-blue: #2a4ea0;
    --brand-mint: #c3dcb8;
    --ink-light: #f2f2f2;
  }
  * { margin: 0; padding: 0; box-sizing: border-box; }
  html, body { width: 1200px; height: 947px; overflow: hidden; background: var(--backdrop); }
  .canvas {
    width: 1200px; height: 947px;
    display: flex; flex-direction: column; align-items: center; justify-content: center;
    gap: 56px;
  }
  .card {
    position: relative;
    width: 660px; height: 377px;
    background: var(--card);
    border-radius: 22px;
    overflow: hidden;
    box-shadow: 0 14px 30px rgba(0,0,0,.45);
  }
  .card--front { display: flex; align-items: center; justify-content: center; }
  .wordmark {
    font-family: "Montserrat", sans-serif;
    font-weight: 700;
    font-size: 96px;
    letter-spacing: 6px;
    color: var(--brand-mint);
  }
  .card--back .brand-disc {
    position: absolute;
    right: -70px; top: -40px;
    width: 340px; height: 340px;
  }
  .details {
    position: absolute;
    left: 48px; bottom: 40px;
    font-family: "Open Sans", sans-serif;
    color: var(--ink-light);
  }
  .person-name {
    font-family: "Montserrat", sans-serif;
    font-weight: 700;
    font-size: 30px;
    color: var(--brand-blue);
    line-height: 1.1;
  }
  .person-role { font-size: 18px; margin-bottom: 34px; }
  .address { font-size: 18px; line-height: 1.3; margin-bottom: 26px; font-style: normal; }
  .contact-list { list-style: none; font-size: 18px; line-height: 1.3; }
  .contact-list li { display: flex; align-items: center; gap: 10px; }
  .contact-list svg { width: 16px; height: 16px; flex: none; }
</style>
</head>
<body>
<main class="canvas">
  <section class="card card--front" aria-label="Card front">
    <span class="wordmark">KORVEN</span>
  </section>

  <section class="card card--back" aria-label="Card back">
    <svg class="brand-disc" viewBox="0 0 340 340" aria-hidden="true">
      <circle cx="170" cy="170" r="130" fill="none" stroke="var(--brand-blue)" stroke-width="40"/>
    </svg>
    <div class="details">
      <h1 class="person-name">Mara Lindqvist</h1>
      <p class="person-role">Chief Operating Officer</p>
      <address class="address">
        48 Harbour Lane,<br>
        Meridian Tower #07-02,<br>
        Singapore 048812
      </address>
      <ul class="contact-list">
        <li>
          <svg viewBox="0 0 16 16" aria-hidden="true"><path fill="var(--brand-blue)" d="M3.5 1.5l2.5 0 1 3.5-1.6 1.2a8 8 0 0 0 4.4 4.4L11 9l3.5 1v2.5c0 1-1 2-2 2C6.5 14.5 1.5 9.5 1.5 3.5c0-1 1-2 2-2z"/></svg>
          +65 9000 4821
        </li>
        <li>
          <svg viewBox="0 0 16 16" aria-hidden="true"><rect x="1" y="3" width="14" height="10" rx="1" fill="var(--brand-blue)"/><path d="M1.5 3.5l6.5 5 6.5-5" fill="none" stroke="var(--card)" stroke-width="1.3"/></svg>
          mara@korven.com
        </li>
        <li>
          <svg viewBox="0 0 16 16" aria-hidden="true"><circle cx="8" cy="8" r="7" fill="var(--brand-blue)"/><path d="M1 8h14M8 1c-3 3-3 11 0 14M8 1c3 3 3 11 0 14" fill="none" stroke="var(--card)" stroke-width="1"/></svg>
          www.korven.com
        </li>
      </ul>
    </div>
  </section>
</main>
</body>
</html>
```